One of a Kind Clean Business Card

We need to design a new business card template for our company. Our company designs and produced merchandising displays. You can see a sample of what we produce on our site www.qorvanexhibits.net. I have uploaded our logo in vector format, as well as a picture of our current business cards. We want a totally different look. We want simple and clean, looking forward to seeing what people create.
Updates

I would like to update the address for Qorvan Fixture Works Inc. 518 E Tollmere Ln Brookvale, IL 60017 Would also note. No QR codes

Industry/Entity Type

Business

Contact Information for Business Card

Need a 1 sided business card designed.

Font styles to use
Serif

Requirements
Must have
• Easy to view; Clean Design
Nice to have
• Features that promote engineering and creativity
Should not have
• Too much clutter, keep it simple

```html
<!DOCTYPE html>
<html lang="en">
<head>
<meta charset="utf-8">
<title>Qorvan Fixture Works Inc. — Business Card</title>
<link href="https://fonts.googleapis.com/css2?family=Arimo:wght@400;700&display=swap" rel="stylesheet">
<style>
  :root {
    --backdrop: #2b2b2b;
    --card: #f7f7f7;
    --ink: #1a1a1a;
    --muted: #333333;
    --brand-red: #8a1a22;
    --stripe-black: #111111;
    --on-red: #ffffff;
  }
  * { margin: 0; padding: 0; box-sizing: border-box; }
  html, body {
    width: 1200px; height: 997px; overflow: hidden;
    background: var(--backdrop);
    font-family: "Arimo", Arial, sans-serif;
  }
  .stage {
    width: 1200px; height: 997px;
    display: flex; align-items: center; justify-content: center;
  }
  .business-card {
    position: relative;
    width: 900px; height: 514px;
    background: var(--card);
    overflow: hidden;
    box-shadow: 0 10px 30px rgba(0,0,0,.45);
  }
  .card-shapes { position: absolute; inset: 0; width: 100%; height: 100%; }

  .wordmark {
    position: absolute; left: 190px; top: 78px;
    display: flex; align-items: center; gap: 14px;
    color: var(--ink);
    font-size: 34px; font-weight: 400; letter-spacing: .5px;
  }
  .wordmark-square { width: 26px; height: 26px; background: var(--brand-red); }

  .holder { position: absolute; left: 70px; top: 272px; }
  .holder-name { font-size: 30px; font-weight: 700; color: var(--ink); letter-spacing: .5px; }
  .holder-role { font-size: 19px; color: var(--brand-red); margin-top: 4px; }

  .contact-list {
    position: absolute; left: 70px; top: 356px;
    list-style: none; font-size: 21px; color: var(--muted);
  }
  .contact-list li { display: flex; align-items: center; gap: 12px; height: 34px; }
  .contact-icon { width: 20px; height: 20px; flex: none; }

  .company-address {
    position: absolute; right: 22px; top: 340px;
    text-align: right; font-size: 18px; color: var(--ink); line-height: 23px;
    font-style: normal;
  }
  .company-name { color: var(--brand-red); font-weight: 700; font-size: 19px; }

  .web-address {
    position: absolute; right: 26px; top: 462px;
    color: var(--on-red); font-size: 18px; font-weight: 700; letter-spacing: 2px;
  }
</style>
</head>
<body>
<main class="stage">
  <article class="business-card">
    <svg class="card-shapes" viewBox="0 0 900 514" aria-hidden="true">
      <line x1="500" y1="140" x2="880" y2="140" stroke="var(--ink)" stroke-width="1.2"/>
      <line x1="350" y1="302" x2="880" y2="302" stroke="var(--ink)" stroke-width="1.2"/>
      <path d="M0 470 L516 470 Q544 470 554 450 L562 456 Q550 482 516 482 L0 482 Z" fill="var(--stripe-black)"/>
      <path d="M0 492 L520 492 Q558 492 572 458 Q584 430 620 430 L900 430 L900 514 L0 514 Z" fill="var(--brand-red)"/>
    </svg>

    <div class="wordmark">
      <span class="wordmark-square"></span>
      <span>Qorvan Fixture Works Inc.</span>
    </div>

    <div class="holder">
      <h1 class="holder-name">DANA WHITLOCK</h1>
      <p class="holder-role">Co-Founder</p>
    </div>

    <ul class="contact-list">
      <li>
        <svg class="contact-icon" viewBox="0 0 20 20" aria-hidden="true"><circle cx="10" cy="10" r="10" fill="var(--brand-red)"/><path d="M6 7 Q6 5 8 5 L9 7 L8 8 Q9 11 12 12 L13 11 L15 12 Q15 14 13 14 Q7 14 6 7Z" fill="#fff"/></svg>
        <span>+44 207 555 0148</span>
      </li>
      <li>
        <svg class="contact-icon" viewBox="0 0 20 20" aria-hidden="true"><circle cx="10" cy="10" r="10" fill="var(--brand-red)"/><rect x="7" y="4.5" width="6" height="11" rx="1.2" fill="#fff"/></svg>
        <span>07700 900315</span>
      </li>
      <li>
        <svg class="contact-icon" viewBox="0 0 20 20" aria-hidden="true"><circle cx="10" cy="10" r="10" fill="var(--brand-red)"/><rect x="5" y="6.5" width="10" height="7" fill="#fff"/><path d="M5 6.5 L10 10.5 L15 6.5" fill="none" stroke="var(--brand-red)" stroke-width="1"/></svg>
        <span>d.whitlock@qorvanexhibits.net</span>
      </li>
    </ul>

    <address class="company-address">
      <div class="company-name">QORVAN FIXTURE WORKS INC.</div>
      <div>518 E Tollmere Ln</div>
      <div>Brookvale, IL 60017</div>
    </address>

    <div class="web-address">www.qorvanexhibits.net</div>
  </article>
</main>
</body>
</html>
```